Create a Big Data Website that is professional but has a creative flare to it.

I am after a modern business design for a company in the Big Data space however it still needs to have a wow value and something stand out from other corporate websites.
My competitors websites are to give you and idea of content:
www.tarnvilla.com
www.pluvoria.com
www.meridu4.com.au
www.quornaby.com
I have uploaded my company Logo so you can use that to make sure it matches your theme.

Target Market(s)

Banks, Insurance Companies, Government, Gas and Energy Companies and Food Manufacturing.

Industry/Entity Type

Consulting

Coding

Number of Pages Required

5+ page

Colors

Designer to choose colors to be used in the design.

Requirements
Must have
• Images, Diagrams around Big Data. Usage of information or graphs from sources like Velsham are fine to use.
Nice to have
• Interactive design use mouse overs, change in text, highlighting information for clear focus.
Should not have
• Cluttered Pages of Informaiton

```html
<!DOCTYPE html>
<html lang="en">
<head>
<meta charset="utf-8">
<title>Keldane Consulting — Big Data</title>
<link href="https://fonts.googleapis.com/css2?family=Raleway:wght@400;500;600;700;800&display=swap" rel="stylesheet">
<style>
:root{
  --blue:#1090d8;
  --blue-bright:#1a9be0;
  --navy:#1c477c;
  --navy-deep:#14305a;
  --ink:#333;
  --muted:#666;
  --beige:#f8f0e6;
  --footer:#2a2a2a;
  --line:#d6d6d6;
  --white:#fff;
}
*{margin:0;padding:0;box-sizing:border-box}
html,body{width:1200px;height:2497px;overflow:hidden;background:var(--white)}
body{position:relative;font-family:"Raleway",Arial,sans-serif;color:var(--ink)}
.abs{position:absolute}

/* hero */
.hero{left:0;top:0;width:1200px;height:589px;background:radial-gradient(ellipse at 70% 30%,#7fc8f2 0%,#3c9ee0 40%,#1e7dc8 75%,#2b8fd6 100%)}
.hero-title{left:97px;top:240px;font-size:57px;font-weight:700;color:var(--white);letter-spacing:.5px}
.hero-sub{left:99px;top:314px;font-size:19px;color:#eaf6ff}
.hero-arrow{top:272px;width:40px;height:40px;border-radius:50%;background:rgba(255,255,255,.35)}
.hero-arrow svg{display:block}

/* header */
.header{left:98px;top:0;width:1002px;height:100px;background:var(--white);box-shadow:0 2px 6px rgba(0,0,0,.08)}
.brand{left:16px;top:32px;display:flex;align-items:center;gap:10px}
.brand-mark{width:34px;height:34px;background:var(--navy);border-radius:50%}
.brand-name{font-size:24px;font-weight:700;color:var(--navy);line-height:1}
.nav{right:115px;top:43px;display:flex;gap:32px;font-size:13.5px;color:#444}
.nav .active{color:var(--blue)}
.nav-extra{right:18px;top:43px;display:flex;gap:36px;align-items:center}
.flag{width:18px;height:12px;background:linear-gradient(#c8102e,#c8102e) center/100% 3px no-repeat,linear-gradient(#c8102e,#c8102e) center/3px 100% no-repeat,#1d3f8f}

/* section headings */
.section-title{left:0;width:1200px;text-align:center;font-size:22px;font-weight:500;color:var(--blue);letter-spacing:.5px}
.rule{left:487px;width:226px;height:1px;background:var(--line)}
.rule::after{content:"";position:absolute;left:103px;top:-1px;width:20px;height:3px;background:var(--blue)}
.lead{left:190px;width:820px;text-align:center;font-size:12.5px;line-height:25px;color:var(--muted)}

/* services */
.service{top:808px;width:240px;text-align:center}
.service svg{display:block;margin:0 auto}
.service h3{margin-top:18px;font-size:15px;font-weight:500;color:#333;letter-spacing:.4px}
.service p{margin-top:9px;font-size:11.5px;line-height:21px;color:var(--muted)}
.service a{display:inline-block;margin-top:6px;font-size:10.5px;color:var(--blue);text-decoration:underline}
.service.current h3{color:var(--navy-deep)}
.service.current a{color:var(--navy)}

/* big data band */
.band{left:0;top:1067px;width:1200px;height:449px;background:var(--beige)}
.band-art{left:100px;top:1067px;width:450px;height:449px;background:radial-gradient(circle at 50% 55%,#ffffff 0%,#f3e3cf 45%,#f8f0e6 75%)}
.band-title{left:591px;top:1126px;font-size:20px;font-weight:500;color:var(--blue)}
.band-text{left:591px;top:1170px;width:480px;font-size:12px;line-height:25px;color:#444}
.band-text p+p{margin-top:18px}
.band-link{left:591px;top:1459px;font-size:12px;font-weight:700;color:var(--navy);text-decoration:underline}

/* solution cards */
.card{top:1674px;width:233px;height:333px;color:var(--white);text-align:center}
.card.light{background:var(--blue-bright)}
.card.dark{background:var(--navy)}
.card-media{height:170px}
.card-icon{position:absolute;left:96px;top:150px;width:40px;height:40px;border-radius:50%;display:flex;align-items:center;justify-content:center}
.card.light .card-icon{background:#0d7fc0}
.card.dark .card-icon{background:var(--navy-deep)}
.card h4{margin-top:42px;font-size:16px;font-weight:500}
.card p{margin:12px 18px 0;font-size:11px;line-height:21px}

/* testimonials */
.divider{left:330px;top:2197px;width:540px;height:1px;background:var(--line)}
.divider::after{content:"";position:absolute;left:265px;top:-4px;width:9px;height:9px;border:1px solid #bbb;border-radius:50%;background:var(--white)}
.quote-avatar{top:2236px;width:110px;height:110px;border-radius:50%}
.quote{top:2252px;width:270px}
.quote .name{font-size:10px;font-weight:700;color:var(--blue)}
.quote .date{margin-top:8px;font-size:9.5px;font-style:italic;color:#333}
.quote .text{margin-top:10px;font-size:11px;line-height:20px;color:var(--muted)}
.chev{top:2268px}

/* footer */
.footer{left:0;top:2403px;width:1200px;height:94px;background:var(--footer)}
.footer-nav{left:100px;top:2427px;display:flex;gap:12px;font-size:10.5px;color:#ddd;letter-spacing:.3px}
.footer-nav span.sep{color:#999}
.copyright{left:100px;top:2461px;font-size:8.5px;color:#aaa;letter-spacing:.3px}
.copyright b{color:var(--blue-bright);font-weight:600;text-decoration:underline}
.social{left:924px;top:2436px;display:flex;gap:9px}
.social span{width:28px;height:28px;border-radius:50%;background:#8a8a8a}
</style>
</head>
<body>

<div class="abs hero" role="img" aria-label="Blue glowing data network of connected nodes and lines"></div>
<div class="abs hero-title">KELDANE CONSULTING</div>
<div class="abs hero-sub">At vero eos et accusamus et iusto odio dignissimos</div>
<div class="abs hero-arrow" style="left:30px"><svg width="40" height="40" viewBox="0 0 40 40"><path d="M23 12l-8 8 8 8" fill="none" stroke="#fff" stroke-width="3"/></svg></div>
<div class="abs hero-arrow" style="left:1131px"><svg width="40" height="40" viewBox="0 0 40 40"><path d="M17 12l8 8-8 8" fill="none" stroke="#fff" stroke-width="3"/></svg></div>

<header class="abs header">
  <div class="abs brand">
    <span class="brand-mark"></span>
    <span class="brand-name">Keldane Consulting</span>
  </div>
  <nav class="abs nav">
    <span class="active">Home</span><span>About</span><span>Solutions</span><span>Clients</span><span>Partners</span><span>News</span><span>Careers</span>
  </nav>
  <div class="abs nav-extra">
    <svg width="14" height="14" viewBox="0 0 14 14"><circle cx="6" cy="6" r="4.2" fill="none" stroke="#1c477c" stroke-width="2"/><path d="M9 9l4 4" stroke="#1c477c" stroke-width="2"/></svg>
    <span class="flag"></span>
  </div>
</header>

<div class="abs section-title" style="top:634px">WELCOME TO OUR COMPANY</div>
<div class="abs rule" style="top:686px"></div>
<div class="abs lead" style="top:710px">At vero eos et accusamus et iusto odio dignissimos ducimus qui blanditiis praesentium voluptatum deleniti atque corrupti quos dolores et quas molestias excepturi sint occaecati cupiditate non provident.</div>

<div class="abs service current" style="left:85px">
  <svg width="86" height="96" viewBox="0 0 86 96"><polygon points="43,3 82,25.5 82,70.5 43,93 4,70.5 4,25.5" fill="none" stroke="#14305a" stroke-width="3"/><ellipse cx="43" cy="37" rx="12" ry="4" fill="#14305a"/><path d="M31 41v7c0 2 5 4 12 4s12-2 12-4v-7c0 2-5 4-12 4s-12-2-12-4zM31 52v7c0 2 5 4 12 4s12-2 12-4v-7c0 2-5 4-12 4s-12-2-12-4z" fill="#14305a"/></svg>
  <h3>DATA WAREHOUSING</h3>
  <p>On the other hand, we denounce with<br>beguiled and demoralized</p>
  <a>READ MORE</a>
</div>
<div class="abs service" style="left:348px">
  <svg width="86" height="96" viewBox="0 0 86 96"><polygon points="43,3 82,25.5 82,70.5 43,93 4,70.5 4,25.5" fill="none" stroke="#1090d8" stroke-width="2"/><rect x="34" y="36" width="13" height="17" fill="none" stroke="#1090d8" stroke-width="2.5"/><rect x="40" y="42" width="13" height="17" fill="#1090d8"/></svg>
  <h3>BUSINESS INTELLIGENCE</h3>
  <p>On the other hand, we denounce with<br>beguiled and demoralized</p>
  <a>READ MORE</a>
</div>
<div class="abs service" style="left:611px">
  <svg width="86" height="96" viewBox="0 0 86 96"><polygon points="43,3 82,25.5 82,70.5 43,93 4,70.5 4,25.5" fill="none" stroke="#1090d8" stroke-width="2"/><path d="M34 60l16-16" stroke="#1090d8" stroke-width="3"/><path d="M50 36v5M47.5 38.5h5M56 42v4M54 44h4" stroke="#1090d8" stroke-width="1.5"/></svg>
  <h3>ADVANCED ANALYTICS</h3>
  <p>On the other hand, we denounce with<br>beguiled and demoralized</p>
  <a>READ MORE</a>
</div>
<div class="abs service" style="left:874px">
  <svg width="86" height="96" viewBox="0 0 86 96"><polygon points="43,3 82,25.5 82,70.5 43,93 4,70.5 4,25.5" fill="none" stroke="#1090d8" stroke-width="2"/><path d="M33 36v22h22" fill="none" stroke="#1090d8" stroke-width="2"/><rect x="37" y="46" width="3" height="10" fill="#1090d8"/><rect x="42" y="42" width="3" height="14" fill="#1090d8"/><rect x="47" y="48" width="3" height="8" fill="#1090d8"/></svg>
  <h3>BIG DATA</h3>
  <p>On the other hand, we denounce with<br>beguiled and demoralized</p>
  <a>READ MORE</a>
</div>

<div class="abs band"></div>
<div class="abs band-art" role="img" aria-label="Illustration of hands using a tablet showing charts, surrounded by business and data icons"></div>
<div class="abs band-title">BIG DATA</div>
<div class="abs band-text">
  <p>At vero eos et accusamus et iusto odio dignissimos ducimus qui blanditiis praesentium voluptatum deleniti atque corrupti quos dolores et quas molestias excepturi sint occaecati cupiditate non provident.</p>
  <p>Sed ut perspiciatis unde omnis iste natus error sit voluptatem accusantium doloremque laudantium, totam rem aperiam, eaque ipsa quae ab illo inventore veritatis et quasi architecto beatae vitae dicta sunt explicabo. Nemo enim ipsam voluptatem quia voluptas sit aspernatur aut odit aut fugit, sed quia consequuntur magni dolores eos qui ratione voluptatem sequi nesciunt. Neque porro quisquam est, qui dolorem ipsum quia dolor sit amet, consectetur.</p>
</div>
<a class="abs band-link">READ MORE</a>

<div class="abs section-title" style="top:1565px">BIG DATA ANALYTICS SOLUTIONS</div>
<div class="abs rule" style="top:1619px"></div>

<div class="abs card light" style="left:98px">
  <div class="card-media" role="img" aria-label="Photo of colleagues reviewing charts on a computer" style="background:linear-gradient(135deg,#c9a98a,#7a8a6a 50%,#3d4a3a)"></div>
  <div class="card-icon"><svg width="16" height="14" viewBox="0 0 16 14"><path d="M1 7h13M9 2l5 5-5 5" fill="none" stroke="#fff" stroke-width="2"/></svg></div>
  <h4>Commercial Strategy</h4>
  <p>At vero eos et accusamus et iusto odio dignissimos ducimus qui blan praesen tium voluptatum...</p>
</div>
<div class="abs card dark" style="left:355px">
  <div class="card-media" role="img" aria-label="Photo of a hand touching floating data network icons" style="background:linear-gradient(135deg,#9aa6b3,#55667a 50%,#2c3a4c)"></div>
  <div class="card-icon"><svg width="16" height="14" viewBox="0 0 16 14"><path d="M1 7h13M9 2l5 5-5 5" fill="none" stroke="#fff" stroke-width="2"/></svg></div>
  <h4>Big Data Platform</h4>
  <p>At vero eos et accusamus et iusto odio dignissimos ducimus qui blan praesen tium voluptatum...</p>
</div>
<div class="abs card light" style="left:611px">
  <div class="card-media" role="img" aria-label="Photo of a glowing light bulb above a notebook" style="background:linear-gradient(135deg,#6f6254,#d8c39a 50%,#4a4038)"></div>
  <div class="card-icon"><svg width="16" height="14" viewBox="0 0 16 14"><path d="M1 7h13M9 2l5 5-5 5" fill="none" stroke="#fff" stroke-width="2"/></svg></div>
  <h4>Insights</h4>
  <p>At vero eos et accusamus et iusto odio dignissimos ducimus qui blan praesen tium voluptatum...</p>
</div>
<div class="abs card dark" style="left:867px">
  <div class="card-media" role="img" aria-label="Photo of a hand reaching into colourful data charts" style="background:linear-gradient(135deg,#1f3b6a,#c0542a 55%,#e2a34a)"></div>
  <div class="card-icon"><svg width="16" height="14" viewBox="0 0 16 14"><path d="M1 7h13M9 2l5 5-5 5" fill="none" stroke="#fff" stroke-width="2"/></svg></div>
  <h4>Data Science</h4>
  <p>At vero eos et accusamus et iusto odio dignissimos ducimus qui blan praesen tium voluptatum...</p>
</div>

<div class="abs section-title" style="top:2055px">TESTIMONIALS</div>
<div class="abs rule" style="top:2102px"></div>
<div class="abs lead" style="top:2121px;left:160px;width:880px">At vero eos et accusamus et iusto odio dignissimos ducimus qui blanditiis praesentium voluptatum deleniti atque corrupti quos dolores et quas molestias excepturi sint occaecati cupiditate non provident.</div>
<div class="abs divider"></div>

<svg class="abs chev" style="left:152px" width="12" height="24" viewBox="0 0 12 24"><path d="M10 2L2 12l8 10" fill="none" stroke="#ccc" stroke-width="1.5"/></svg>
<svg class="abs chev" style="left:1036px" width="12" height="24" viewBox="0 0 12 24"><path d="M2 2l8 10-8 10" fill="none" stroke="#ccc" stroke-width="1.5"/></svg>

<div class="abs quote-avatar" style="left:198px;background:linear-gradient(#d9cfc7,#b7a597)" role="img" aria-label="Portrait of a smiling client"></div>
<div class="abs quote" style="left:338px">
  <div class="name">NEMO ENIM IPSAM</div>
  <div class="date">Posted on 29 Sep 2017</div>
  <div class="text">At vero eos et accusamus et iusto odio dignissimos ducimus qui praesentium.</div>
</div>
<div class="abs quote-avatar" style="left:627px;background:linear-gradient(#d4dce4,#9aa9b8)" role="img" aria-label="Portrait of a smiling client"></div>
<div class="abs quote" style="left:766px">
  <div class="name">NEMO ENIM IPSAM</div>
  <div class="date">Posted on 29 Sep 2017</div>
  <div class="text">At vero eos et accusamus et iusto odio dignissimos ducimus qui praesentium.</div>
</div>

<footer class="abs footer"></footer>
<div class="abs footer-nav"><span>HOME</span><span class="sep">/</span><span>ABOUT</span><span class="sep">/</span><span>SOLUTIONS</span><span class="sep">/</span><span>CLIENTS</span><span class="sep">/</span><span>PARTNERS</span><span class="sep">/</span><span>NEWS</span><span class="sep">/</span><span>CAREERS</span></div>
<div class="abs copyright">© COPYRIGHT 2017. <b>KELDANE CONSULTING</b>. ALL RIGHTS RESERVED.</div>
<div class="abs social"><span></span><span></span><span></span><span></span><span></span></div>

</body>
</html>
```